QAMBRO THERAPEUTICS

physical therapy company. need a flashy image and named logo, website link, that I can also use on Letterhead and business cards. Clean, sharp, modern, eye catching. 3 colors? Some shine. Needs to stand out and not be trendy or too much cursive . Androgynous image of a human body is ok. A spine included is ok. Prefer lines to curves for font types. Warm colors but strong impact. Will need to have some contact info and border mission statement on it.
Updates

Target Market(s)

Target market is large corporations, wealthy individuals, medical doctors

Industry/Entity Type

Medical, physical therapy

Contact Information for Business Card

Name, Owner, phone, email, and website

Colors
0054AA
0677BA
7BADD7
CADEEF
E8F1F8

Requirements
Must have
• See above- something about BALANCE, wellness, strength etc
Nice to have
• Contrast, depth
Should not have
• No cursive

```html
<!DOCTYPE html>
<html lang="en">
<head>
<meta charset="UTF-8">
<title>Qambro Therapeutics – Business Card</title>
<link rel="stylesheet" href="https://fonts.googleapis.com/css2?family=Cinzel:wght@700&family=Poppins:wght@400&display=swap">
<style>
  :root {
    --brand-blue: #0054AA;
    --ink: #2a2a2a;
    --rule: #8a8a8a;
    --card-bg: #f5f3f4;
    --card-bg-edge: #ecebee;
    --stage: #e6e7ea;
    --panel-deep: #0b1a4d;
    --panel-mid: #0f3f95;
    --panel-light: #6aa6dc;
  }
  html, body {
    margin: 0;
    width: 1200px;
    height: 900px;
    overflow: hidden;
    background: var(--stage);
  }
  .business-card {
    position: absolute;
    left: 100px;
    top: 141px;
    width: 1000px;
    height: 618px;
    background: linear-gradient(135deg, var(--card-bg) 0%, var(--card-bg-edge) 100%);
    box-shadow: 0 14px 40px rgba(0,0,0,0.18);
    overflow: hidden;
    font-family: "Poppins", sans-serif;
  }
  .hero-illustration {
    position: absolute;
    top: 0;
    right: 0;
    width: 270px;
    height: 100%;
    background:
      radial-gradient(ellipse 80% 55% at 45% 70%, var(--panel-light) 0%, var(--panel-mid) 55%, transparent 100%),
      linear-gradient(180deg, var(--panel-deep) 0%, var(--panel-mid) 100%);
  }
  .company-name {
    position: absolute;
    left: 39px;
    top: 88px;
    margin: 0;
    font-family: "Cinzel", serif;
    font-weight: 700;
    font-size: 46px;
    letter-spacing: 0.5px;
    color: var(--brand-blue);
    white-space: nowrap;
  }
  .person {
    position: absolute;
    left: 42px;
    top: 296px;
  }
  .person-name {
    margin: 0;
    font-family: "Cinzel", serif;
    font-weight: 700;
    font-size: 33px;
    line-height: 1.1;
    color: var(--brand-blue);
  }
  .person-role {
    margin: 0;
    font-size: 27px;
    line-height: 1.3;
    color: var(--ink);
  }
  .divider {
    position: absolute;
    left: 43px;
    top: 390px;
    width: 66px;
    height: 1px;
    background: var(--rule);
  }
  .contact-list {
    position: absolute;
    left: 42px;
    top: 430px;
    margin: 0;
    padding: 0;
    list-style: none;
  }
  .contact-item {
    display: flex;
    align-items: center;
    height: 38px;
    font-size: 28px;
    color: var(--ink);
  }
  .contact-icon {
    width: 26px;
    height: 26px;
    margin-right: 12px;
    fill: none;
    stroke: var(--brand-blue);
    stroke-width: 2;
  }
  .contact-icon.solid { fill: var(--brand-blue); stroke: none; }
  .web-name { color: var(--brand-blue); }
</style>
</head>
<body>
  <section class="business-card">
    <div class="hero-illustration" role="img" aria-label="Illustration of a running human figure in blue with the skeleton visible and the knee joints highlighted in orange"></div>

    <h1 class="company-name">QAMBRO THERAPEUTICS</h1>

    <div class="person">
      <p class="person-name">DANIEL HARLOW</p>
      <p class="person-role">Managing Director</p>
    </div>

    <div class="divider"></div>

    <ul class="contact-list">
      <li class="contact-item">
        <svg class="contact-icon" viewBox="0 0 24 24" aria-hidden="true">
          <path d="M5 3h4l2 5-2.5 1.5a11 11 0 0 0 6 6L16 13l5 2v4a2 2 0 0 1-2 2A16 16 0 0 1 3 5a2 2 0 0 1 2-2z"/>
          <path d="M14 3a7 7 0 0 1 7 7M14 7a3 3 0 0 1 3 3"/>
        </svg>
        044-987 654 321
      </li>
      <li class="contact-item">
        <svg class="contact-icon solid" viewBox="0 0 24 24" aria-hidden="true">
          <path d="M2 5h20v14H2z M2 5l10 8 10-8" />
          <path d="M2 5l10 8 10-8" fill="none" stroke="#f5f3f4" stroke-width="1.6"/>
        </svg>
        info@qambrotherapy.com
      </li>
      <li class="contact-item">
        <svg class="contact-icon" viewBox="0 0 24 24" aria-hidden="true">
          <circle cx="12" cy="12" r="9.5"/>
          <ellipse cx="12" cy="12" rx="4" ry="9.5"/>
          <path d="M2.5 12h19M4 7h16M4 17h16"/>
        </svg>
        <span>www.<span class="web-name">qambrotherapy</span>.com</span>
      </li>
    </ul>
  </section>
</body>
</html>
```